Superfood Organic Powder needs a new Standup Pouch Design

Superfood brand needs a new package design Standup pouch

We need a new packaging design
*Standup Pouch*
for a NEW superfood product to our brand PureLeafy.

This product is a superfood blend of organic powders such as spiralina, chlorella, wheatgrass etc.

The design should be modern with an organic look, - but feel free to play around with it as you wish.

Our first or *older* product is called Vital Blendo, and contains superfood powders like Maca, Moringa, Baobab, Spirulina, Chlorella, Wheatgrass

Find measurements for the standup pouch in the attachments.

We can either go with a

a white standup pouch with a slight opacity to it
(see attached sample I have from my supplier)

or

mat white standup pouch

Or Natural Kraft if

The white pouch with a slight opacity to it so you can see the powder through the pouch. One cool thing about this one is that if we have an area in the design with no colors, not even white, that area will be completely transparent, see picture of the sample pouch we have in the attachments.
In the sample photo the spider is completely transparent.

The Mat white pouch is just a basic white standup pouch with a mat finish.
What ever you think is best for your design you can suggest.

In the future we will create multiple products, each product should have its own color style to distinguish between them - this product should use green Color code as one of the green colors used in the logo. Of course not all colors should have that code, but just the identifier for this product. Please present an idea to showcase this identifier, it could be a thick horizontal or vertical line somewhere on the pouch.

The standup pouch will be digitally printed so we can use all areas of the pouch.

Please provide 3D mockup of the design in order to better get an idea of the design.
Remember that I consider you as the expert so I'm very open to any suggestions regarding this design - in the end the main goal is to attract customers and that is your area of expertise.

Please let me know if you have any questions - thanks in advance

I'm looking forward to working with you.

Here are some links I have found that I think is great designs just to give a little insight to my designs wishes.:

https://www.pinboardly.example/pin/100000000000000001/ https://www.verdanthusk.example/collections/all-superfood-products
https://www.pinboardly.example/pin/100000000000000002/
https://designduel.example/product-label-design/contests/print-design-stand-up-resealable-pouch-organic-spice-100003
https://www.pinboardly.example/pin/100000000000000004/
https://www.pinboardly.example/pin/10000000000000005/
https://www.pinboardly.example/pin/100000000000000006/
https://www.pinboardly.example/pin/100000000000000007/ https://www.pinboardly.example/pin/100000000000000008/
https://www.pinboardly.example/pin/10000000000000009/

Reason: Needed more work because I changed manufacturer of standup pouches.

Target Market(s)

Vegans, Organic interested clients, healthy living, Fitness, Juicers

Industry/Entity Type

Health And Wellness

Requirements
Must have
• The following text should be added on front of the label under the product name:
• Danish certified organic
• Superfood blend
• —
• The product contains the following ingredients and should be mentioned on the front - only the ingredients names:
• Maca, Moringa, Baobab, Spirulina, Chlorella, Wheatgrass
• —
• Organic logo:
• Organic EU logo should be present on the back (find logo in the attachments) To the right of the logo the following text is mandatory with Myriad Pro Regular as a type-font: See previous design for instructions.
• "EU-LOGO-HERE"
• DK-ØKO-000
• EU/ikke-EU-jordbrug
• EU/non-EU Agriculture
• Next to the EU organic logo we will place the danish organic logo which is attached as well, you can decide if it should be on the left or right side, it is a red Ø logo ( find in the attachments as well.
• —
• The label should contain a Nutritional Information with the danish language as primary. By law in Denmark the language used should be danish but it is allowed to add the English word after the danish separated by a /
• So it should be titled as Næringsindhold / Nutritional information (Title Bold font)
• And contain the following:
• energi (KJ/kcal)
• • fedt / fat (g)
• • - heraf mættede fedtsyrer / from saturated fat (g)
• • kulhydrat / carbohydrates (g)
• • - heraf sukkerarter / from sugar (g)
• • protein (g)
• • salt (g)
• • kostfibre / dietary fiber (g)
• —
• We need ingredients list on the back as well titled Ingredienser / Ingredients (Title Bold font)
• Maca, Moringa, Baobab, Spirulina, Chlorella, Hvedegræs / Wheatgrass
• Nettovægt / Netto weight 225 gr
• —-
• You can add some cool logos indicating that the product is:
• 100 % organic
• 100% vegan
• No additives
• Non-GMO
• Gluten free
• —
• Instructions (Title Bold font)
• Mix the superfood powder into 250 ml water with a twist of lemon, coconut water, green juice, smoothies, almond milk, or add to your favorit morning meal.
• Serving size 1-2 teaspoon
• Would be great with 3-4 images describing the instructions
• Image 1 could be fruit being put in a blender
• Image 2 could be 1 teaspoon with powder on top of a blender
• Image 3 could be a blender in use
• Image 4 poring the smoothie in to a glass to enjoy
• —
• Opbevaring / Storage (Title Bold font)
• Opbevares tørt og ikke for varmt
• Keep in a cool and dry place away from sunlight
• —
• Batch: (Title Bold font)
• Best before / Bedst før: (Title Bold font)
• —
• Barcode field
• Make room for a barcode
• —
• Produced in EU for: (Title Bold font)
• Kornvik IVS
• Tranebærvej 42
• 8960 Randers SØ
• Denmark
• www.pureleafy-shop.example (make this bold as well)
• —
• Follow us (Title Bold font)
• Instagram and facebook logo on the back with hashtag #pureleafyshop
• —
• Other than that pureleafy logo can be added as well, it is attached as well.
• I will attach our logo with original AI files.
• —
• Our mission (text)
• We want to provide our customers with the best possible superfood blends. Allowing our customers to get a product packed with antioxidants, vitamins and minerals to elevate their health to the next level. All our products are vegan friendly and GMO free - produced under the best possible circumstances.
• —
Nice to have
• Green color from the logo can be used to get it streamlined.
• Color code c2ce48

```html
<!DOCTYPE html>
<html lang="en">
<head>
<meta charset="utf-8">
<title>PureLeafy – Vital Blendo Standup Pouch</title>
<link href="https://fonts.googleapis.com/css2?family=Kaushan+Script&family=Josefin+Sans:wght@300&family=Lato:wght@400;700&display=swap" rel="stylesheet">
<style>
  :root {
    --backdrop: #e6e6e6;
    --pouch-white: #f7f7f7;
    --gusset: #e1e1e1;
    --brand-green: #4a9a45;
    --deep-green: #2f7a33;
    --lime: #c2ce48;
    --lime-text: #b3c42f;
    --ink-dark: #3a3a3a;
    --seal-line: #9a9a9a;
  }
  html, body {
    margin: 0;
    width: 1200px;
    height: 1200px;
    overflow: hidden;
    background: var(--backdrop);
  }
  .pouch-stage {
    position: relative;
    width: 1200px;
    height: 1200px;
  }
  .pouch {
    position: absolute;
    left: 290px;
    top: 100px;
    width: 620px;
    height: 994px;
  }
  .script { font-family: "Kaushan Script", cursive; }
  .brand-name { font-family: "Josefin Sans", sans-serif; font-weight: 300; }
  .sans { font-family: "Lato", sans-serif; }
</style>
</head>
<body>
<main class="pouch-stage">
  <svg class="pouch" viewBox="0 0 620 994" xmlns="http://www.w3.org/2000/svg">
    <!-- pouch body -->
    <rect class="pouch-body" x="0" y="0" width="620" height="994" fill="var(--pouch-white)"/>
    <rect class="side-seal-left" x="0" y="110" width="26" height="884" fill="var(--gusset)"/>
    <rect class="side-seal-right" x="594" y="110" width="26" height="884" fill="var(--gusset)"/>

    <!-- product colour identifier band -->
    <path class="identifier-band" d="M0 0 H620 V88 C560 92 520 84 470 94 C420 100 380 86 320 96 C260 104 200 90 140 100 C90 106 50 96 26 110 L0 112 Z" fill="var(--brand-green)"/>
    <text class="script" x="310" y="66" text-anchor="middle" font-size="38" fill="#ffffff" transform="rotate(-2 310 60)">Danish Certified Organic</text>

    <!-- tear notch line -->
    <line class="tear-line" x1="26" y1="112" x2="594" y2="112" stroke="var(--seal-line)" stroke-width="1" stroke-dasharray="3 3"/>
    <text class="sans" x="55" y="124" font-size="8" fill="#666">Tear To Open</text>
    <text class="sans" x="565" y="124" font-size="8" fill="#666" text-anchor="end">Tear To Open</text>

    <!-- zipper seal -->
    <rect class="zipper" x="26" y="136" width="568" height="14" fill="#ececec"/>
    <line x1="26" y1="150" x2="594" y2="150" stroke="#dcdcdc" stroke-width="1"/>

    <!-- brand -->
    <circle class="brand-dot" cx="310" cy="222" r="12" fill="var(--lime)"/>
    <text class="brand-name" x="310" y="292" text-anchor="middle" font-size="54" letter-spacing="3" fill="var(--brand-green)">PureLeafy</text>

    <!-- product name on brush disc -->
    <circle class="name-disc" cx="306" cy="546" r="196" fill="var(--brand-green)"/>
    <g class="product-name script" fill="#ffffff" text-anchor="middle" transform="rotate(-8 306 546)">
      <text x="300" y="530" font-size="104">Vital</text>
      <text x="318" y="632" font-size="98">Blendo</text>
    </g>

    <!-- ingredient line -->
    <g class="ingredients sans" font-size="20" fill="var(--lime-text)" text-anchor="middle" letter-spacing="0.5">
      <text x="310" y="760">MACA, MORINGA, BAOBAB, SPIRULINA,</text>
      <text x="310" y="786">CHLORELLA, WHEATGRASS</text>
    </g>

    <!-- claim badges -->
    <g class="claim-badges" fill="#ffffff" stroke="var(--lime)" stroke-width="6">
      <circle cx="151" cy="858" r="32"/>
      <circle cx="234" cy="858" r="32"/>
      <circle cx="318" cy="858" r="32"/>
      <circle cx="402" cy="858" r="32"/>
      <circle cx="486" cy="858" r="32"/>
    </g>
    <g class="claim-labels sans" font-size="9" fill="var(--ink-dark)" text-anchor="middle" letter-spacing="0.3">
      <text x="151" y="906">100% ORGANIC</text>
      <text x="234" y="906">NON-GMO</text>
      <text x="318" y="906">100% VEGAN</text>
      <text x="402" y="906">GLUTEN FREE</text>
      <text x="486" y="906">NO PRESERVATIVE</text>
    </g>

    <!-- net weight -->
    <text class="net-weight sans" x="310" y="952" text-anchor="middle" font-size="20" letter-spacing="1" fill="var(--deep-green)">225 GM</text>
  </svg>
</main>
</body>
</html>
```